Bramwell Policy Lookout Hub

I want a landing page for them to click on the logo with a brief description of the site.

Once they click on the logo, it will take them to make a decision for two types of insurance. One will be health and the other will be home/auto.

I will need an iframe for the home/auto and it will take them to a site (which is already built) for them to get a quote.

I will need a separate iframe for the health to take them to separate site (which is built) for them to get a quote.

Target Market(s)

18-45 Year olds who want to go online for insurance quotes. This is for quoting primarily and not an information site.

Industry/Entity Type

Health

Requirements
Must have
• Sleek and sexy. I have a logo as well.

May want the following on the landing page:
Georgia's FIRST Insurance Exchange for Home, Auto, and Health Insurance

No Hassle, Real-time, Quotes - As a Matter of fact... You call us if interested, We dont sell your information and Most Importantly… its free!!

Give it a shot… Click on the logo to get started and if you are interested in one of the many carriers we represent, call us.
Should not have
• Don't want the typical website. I want this to be different than all template boxes.

```html
<!DOCTYPE html>
<html lang="en">
<head>
<meta charset="utf-8">
<title>Bramwell Policy Lookout Hub</title>
<link href="https://fonts.googleapis.com/css2?family=Oswald:wght@400;500&family=Alfa+Slab+One&family=Arimo:wght@400;700&family=Open+Sans:wght@400&display=swap" rel="stylesheet">
<style>
  :root {
    --red-top: #d01d2e;
    --red-bottom: #7c0a17;
    --red-divider: #5e0711;
    --blue-deep: #0a5f9c;
    --blue-mid: #0c7fc1;
    --blue-light: #19a6e0;
    --navy-top: #17344a;
    --navy-bottom: #0a1a26;
    --white: #ffffff;
    --yellow: #fff200;
    --logo-ink: #1f1f1f;
    --bullet: #e23a12;
  }
  * { margin: 0; padding: 0; box-sizing: border-box; }
  html, body { width: 1200px; height: 673px; overflow: hidden; }
  body { font-family: "Arimo", Arial, sans-serif; background: var(--blue-mid); }

  .page {
    position: relative; width: 1200px; height: 673px; overflow: hidden;
    background: linear-gradient(180deg, var(--blue-deep) 0%, var(--blue-mid) 45%, #0a6aa8 100%);
  }

  .top-bar {
    position: absolute; left: 0; top: 0; width: 1200px; height: 78px;
    background: linear-gradient(180deg, var(--red-top) 0%, #a9101f 55%, var(--red-bottom) 100%);
  }
  .main-nav { position: absolute; right: 0; top: 0; height: 78px; display: flex; }
  .main-nav a {
    display: flex; align-items: center; justify-content: center;
    height: 78px; color: var(--white); text-decoration: none;
    font-family: "Oswald", "Arial Narrow", sans-serif; font-weight: 400;
    font-size: 25px; letter-spacing: 0.5px; text-transform: uppercase;
  }
  .main-nav .nav-home { width: 134px; }
  .main-nav .nav-quote { width: 221px; border-left: 1px solid var(--red-divider); }
  .main-nav .nav-contact { width: 206px; border-left: 1px solid var(--red-divider); }

  .brand-box {
    position: absolute; left: 24px; top: 0; width: 202px; height: 150px;
    background: var(--white); display: flex; flex-direction: column;
    align-items: center; justify-content: center; gap: 10px; text-decoration: none;
  }
  .brand-mark { width: 34px; height: 34px; border-radius: 50%; background: var(--red-top); }
  .brand-name {
    color: var(--logo-ink); font-family: "Arimo", Arial, sans-serif; font-weight: 700;
    font-size: 17px; line-height: 21px; text-align: center; text-transform: uppercase;
  }

  .cover-art {
    position: absolute; left: 587px; top: 168px; width: 613px; height: 439px;
    background: radial-gradient(ellipse at 55% 45%, var(--blue-light) 0%, rgba(20,140,205,0.55) 45%, rgba(10,100,165,0) 80%);
  }

  .lines {
    position: absolute; right: 6px; top: 100px; display: flex; align-items: center;
  }
  .line-item {
    display: flex; align-items: center; margin-left: 22px;
    font-family: "Alfa Slab One", Georgia, serif; font-size: 46px; color: var(--white);
    text-shadow: 2px 3px 0 #0b2c44, 3px 4px 4px rgba(0,0,0,0.5);
  }
  .line-item .bullet {
    width: 30px; height: 30px; border-radius: 50%; margin-right: 12px;
    background: radial-gradient(circle at 38% 35%, #ff7a3d 0%, var(--bullet) 50%, #8d1604 100%);
    box-shadow: 0 2px 3px rgba(0,0,0,0.5);
  }

  .intro {
    position: absolute; left: 25px; top: 190px; width: 630px;
    color: var(--white); font-size: 26px; line-height: 34.5px;
  }
  .intro p { margin-bottom: 35px; }
  .intro .highlight { color: var(--yellow); font-weight: 700; text-transform: uppercase; }

  .site-footer {
    position: absolute; left: 0; top: 607px; width: 1200px; height: 66px;
    background: linear-gradient(180deg, var(--navy-top) 0%, var(--navy-bottom) 100%);
    display: flex; align-items: center; justify-content: center;
    color: var(--white); font-family: "Open Sans", Arial, sans-serif; font-size: 17px;
  }
</style>
</head>
<body>
<div class="page">
  <header class="top-bar">
    <nav class="main-nav">
      <a class="nav-home" href="#">Home Page</a>
      <a class="nav-quote" href="#">Quote Request</a>
      <a class="nav-contact" href="#">Contact Us</a>
    </nav>
  </header>

  <a class="brand-box" href="#">
    <span class="brand-mark"></span>
    <span class="brand-name">Bramwell Policy<br>Lookout Hub</span>
  </a>

  <div class="cover-art" role="img" aria-label="Large glowing word Insurance over a blue digital interface backdrop"></div>

  <div class="lines">
    <div class="line-item"><span class="bullet"></span>HOME</div>
    <div class="line-item"><span class="bullet"></span>AUTO</div>
    <div class="line-item"><span class="bullet"></span>HEALTH</div>
  </div>

  <section class="intro">
    <p>Georgia's FIRST Insurance Exchange for Home, Auto, and Health Insurance</p>
    <p>No Hassle, Real-time, Quotes - As a Matter of fact... You call us if interested, We dont sell your information and Most Importantly… <span class="highlight">its free!!</span></p>
    <p>Give it a shot… <span class="highlight">Click on the logo to get started</span> and if you are interested in one of the many carriers we represent, call us.</p>
  </section>

  <footer class="site-footer">© 2013, All Rights Reserved,&nbsp; Bramwellhub.com</footer>
</div>
</body>
</html>
```